TV Antenna Installation business needs a unique flyer

We need a simple but effective flyer design for our TV Aerial installation company based in Newcastle, NSW, Australia called Bright Harbour TV & Aerial Svcs.
We are trying to target areas where there has been a new transmitter installed and most houses just require their aerial redirecting and tv's retuning.

Industry/Entity Type

Business

Requirements
Must have
• We would like the idea of a headline phrase such as " Poor TV reception……..now a thing from the past" or something similar & catchy.
Also "Did you know a new transmitter has been recently installed in your area, we can therefore now GUARANTEE 100% PERFECT PICTURE
Charges from only $95.
- Free 5 year warranty
- Free signal testing
- Free Onsite Quote
Phone 0463 527 209
Nice to have
• Other services include:

- New Installs
- Extra Points & repairs
- TV wall mounting/Home Cinema
- Pull down tall masts

Modern tv picture, see example uploaded

```html
<!DOCTYPE html>
<html lang="en">
<head>
<meta charset="utf-8">
<title>Bright Harbour TV &amp; Aerial Svcs – Flyer</title>
<link href="https://fonts.googleapis.com/css2?family=Roboto+Condensed:wght@400;700&family=Open+Sans:wght@400&display=swap" rel="stylesheet">
<style>
  :root {
    --red: #e8262b;
    --red-dark: #c4161c;
    --blue: #0b5aa8;
    --blue-deep: #0a3f8c;
    --sky: #5ab4ea;
    --orange: #ee5a24;
    --orange-light: #f57f3a;
    --paper: #f5f5f3;
    --ink: #333333;
    --white: #ffffff;
  }
  * { margin: 0; padding: 0; box-sizing: border-box; }
  html, body { width: 948px; height: 1200px; overflow: hidden; background: var(--paper); }
  .flyer {
    position: relative; width: 948px; height: 1200px; overflow: hidden;
    background: var(--paper);
    font-family: "Roboto Condensed", "Arial Narrow", sans-serif;
  }
  .corner-swoosh { position: absolute; left: 0; top: 0; }
  .business-name {
    position: absolute; left: 98px; top: 38px; width: 790px;
    font-size: 55px; font-weight: 700; color: var(--red); letter-spacing: 0.3px;
    text-shadow: 1px 2px 2px rgba(0,0,0,0.2); white-space: nowrap;
  }
  .location {
    position: absolute; right: 76px; top: 112px;
    font-size: 33px; font-weight: 700; color: var(--blue);
  }
  .headline-bubble { position: absolute; left: 48px; top: 132px; }
  .headline-text {
    position: absolute; left: 78px; top: 190px; width: 220px;
    transform: rotate(-14deg); text-align: center;
    font-size: 36px; font-weight: 700; line-height: 1.08; color: var(--white);
    text-shadow: 1px 2px 2px rgba(0,0,0,0.3);
  }
  .tv-illustration {
    position: absolute; left: 330px; top: 160px; width: 200px; height: 290px;
    border-radius: 30px;
    background: linear-gradient(160deg, #f2dc55, #d8b61f);
  }
  .services-title {
    position: absolute; left: 575px; top: 222px;
    font-size: 40px; font-weight: 700; color: var(--blue);
  }
  .services-list { position: absolute; left: 575px; top: 286px; list-style: none; }
  .services-list li {
    position: relative; padding-left: 36px; margin-bottom: 10px;
    font-size: 27px; font-weight: 700; color: var(--ink); line-height: 1.2;
  }
  .services-list svg { position: absolute; left: 0; top: 6px; }
  .promo-band {
    position: absolute; left: 41px; top: 496px; width: 862px; height: 92px;
    background: linear-gradient(180deg, var(--orange-light), var(--orange));
    color: var(--white); text-align: center;
  }
  .promo-intro { font-size: 19px; font-weight: 700; margin-top: 10px; }
  .promo-guarantee { font-size: 33px; font-weight: 700; margin-top: 6px; }
  .promo-guarantee strong { font-size: 35px; }
  .room-photo {
    position: absolute; left: 41px; top: 588px; width: 720px; height: 324px;
    background: linear-gradient(135deg, #d9b36a 0%, #b07a35 45%, #5c3a1c 100%);
  }
  .side-panel {
    position: absolute; left: 761px; top: 588px; width: 142px; height: 324px;
    background: linear-gradient(180deg, #1a6cc0, var(--blue-deep));
  }
  .product-shot {
    position: absolute; left: 664px; width: 224px; height: 136px;
    border-radius: 12px; border: 4px solid var(--white);
    box-shadow: 0 2px 6px rgba(0,0,0,0.3);
  }
  .product-mount { top: 614px; background: linear-gradient(135deg, #f4f4f4, #9aa4ae); }
  .product-cinema { top: 772px; background: linear-gradient(180deg, #5d8fd6, #dfe7f0 55%, #4a4a4a); }
  .price-tab {
    position: absolute; left: 57px; top: 868px; width: 436px; height: 60px;
    background: linear-gradient(180deg, var(--orange-light), var(--orange));
    border-radius: 14px 14px 0 0;
    color: var(--white); font-size: 34px; font-weight: 700;
    line-height: 60px; padding-left: 40px;
    text-shadow: 1px 1px 2px rgba(0,0,0,0.3);
  }
  .benefits { position: absolute; left: 62px; top: 960px; list-style: none; }
  .benefits li {
    position: relative; padding-left: 36px; margin-bottom: 8px;
    font-size: 35px; font-weight: 700; color: var(--blue); line-height: 1.12;
  }
  .benefits li::before {
    content: ""; position: absolute; left: 0; top: 12px;
    width: 20px; height: 20px; border-radius: 50%; background: var(--orange);
  }
  .target-note {
    position: absolute; left: 508px; top: 970px; width: 400px;
    font-family: "Open Sans", Arial, sans-serif;
    font-size: 14px; line-height: 1.4; color: var(--ink);
  }
  .footer-wave { position: absolute; left: 0; bottom: 0; }
  .call-line {
    position: absolute; left: 420px; top: 1124px;
    color: var(--white); font-size: 42px; font-weight: 700;
    text-shadow: 1px 2px 3px rgba(0,0,0,0.35);
  }
  .call-line .number { font-size: 50px; }
</style>
</head>
<body>
<main class="flyer">
  <svg class="corner-swoosh" width="200" height="150" viewBox="0 0 200 150" aria-hidden="true">
    <path d="M0 0 H200 C120 8 50 50 0 150 Z" fill="var(--blue)"/>
    <path d="M0 150 C40 60 110 16 200 4 L200 12 C120 24 60 70 12 150 Z" fill="var(--orange)"/>
    <path d="M12 150 C60 72 120 28 200 16 L200 22 C124 34 66 80 22 150 Z" fill="var(--white)"/>
  </svg>

  <h1 class="business-name">Bright Harbour TV &amp; Aerial Svcs</h1>
  <p class="location">Newcastle, NSW, Australia</p>

  <svg class="headline-bubble" width="300" height="300" viewBox="0 0 300 300" aria-hidden="true">
    <defs>
      <radialGradient id="bubbleFill" cx="40%" cy="35%" r="70%">
        <stop offset="0" stop-color="#f2444a"/>
        <stop offset="1" stop-color="var(--red-dark)"/>
      </radialGradient>
    </defs>
    <path d="M235 210 L285 262 L205 240 Z" fill="var(--red-dark)" stroke="var(--white)" stroke-width="5"/>
    <circle cx="140" cy="140" r="128" fill="url(#bubbleFill)" stroke="var(--white)" stroke-width="6"/>
  </svg>
  <p class="headline-text">Poor TV Reception? Now a thing from the Past</p>

  <div class="tv-illustration" role="img" aria-label="Illustration of a yellow retro television set with antennas and a signal line on screen"></div>

  <h2 class="services-title">Other services:</h2>
  <ul class="services-list">
    <li><svg width="24" height="24" viewBox="0 0 24 24" aria-hidden="true"><rect x="1" y="3" width="18" height="18" fill="var(--white)" stroke="var(--blue)" stroke-width="2"/><path d="M5 12 L10 17 L22 2" fill="none" stroke="var(--red)" stroke-width="3"/></svg>New Installs</li>
    <li><svg width="24" height="24" viewBox="0 0 24 24" aria-hidden="true"><rect x="1" y="3" width="18" height="18" fill="var(--white)" stroke="var(--blue)" stroke-width="2"/><path d="M5 12 L10 17 L22 2" fill="none" stroke="var(--red)" stroke-width="3"/></svg>Extra Points &amp; repairs</li>
    <li><svg width="24" height="24" viewBox="0 0 24 24" aria-hidden="true"><rect x="1" y="3" width="18" height="18" fill="var(--white)" stroke="var(--blue)" stroke-width="2"/><path d="M5 12 L10 17 L22 2" fill="none" stroke="var(--red)" stroke-width="3"/></svg>TV wall mounting/<br>Home Cinema</li>
    <li><svg width="24" height="24" viewBox="0 0 24 24" aria-hidden="true"><rect x="1" y="3" width="18" height="18" fill="var(--white)" stroke="var(--blue)" stroke-width="2"/><path d="M5 12 L10 17 L22 2" fill="none" stroke="var(--red)" stroke-width="3"/></svg>Pull down tall masts</li>
  </ul>

  <section class="promo-band">
    <p class="promo-intro">Did you know a new transmitter has been recently installed in your area, we can therefore</p>
    <p class="promo-guarantee">now <strong>GUARANTEE 100% PERFECT PICTURE</strong></p>
  </section>

  <div class="room-photo" role="img" aria-label="Photo of a modern living room with a wall-mounted flat screen TV, speakers and lit shelving"></div>
  <div class="side-panel"></div>
  <div class="product-shot product-mount" role="img" aria-label="Photo of a flat screen TV on a swivel wall bracket"></div>
  <div class="product-shot product-cinema" role="img" aria-label="Photo of home cinema equipment with projector screen, player and remote"></div>

  <p class="price-tab">Charges from only $95</p>

  <ul class="benefits">
    <li>Free 5 Year Warranty</li>
    <li>Free Signal Testing</li>
    <li>Free Onsite Quote</li>
  </ul>

  <p class="target-note">We are trying to target areas where there has been a new transmitter installed and most houses just require their aerial redirecting and tv's retuning.</p>

  <svg class="footer-wave" width="948" height="170" viewBox="0 0 948 170" aria-hidden="true">
    <path d="M0 80 C200 20 420 110 640 60 C780 30 880 20 948 30 V170 H0 Z" fill="var(--sky)" opacity="0.55"/>
    <path d="M0 100 C220 40 430 120 650 74 C790 46 890 44 948 52 V170 H0 Z" fill="var(--white)"/>
    <path d="M0 112 C230 56 440 130 660 88 C800 62 895 62 948 70 V170 H0 Z" fill="var(--sky)"/>
    <path d="M0 126 C240 74 450 140 670 104 C810 82 900 82 948 88 V170 H0 Z" fill="var(--blue)"/>
  </svg>
  <p class="call-line">Call: <span class="number">0463 527 209</span></p>
</main>
</body>
</html>
```